High Tech Real Estate Startup needs a business card

We are developing an innovative real estate marketing product based around advanced search and virtual reality.

We talk to people, we need business cards.

Target Market(s)

The target market is technology professionals and realtors.

Contact Information for Business Card

The information to be included will include

Name
Title
Phone Number
E-mail Address
www.zelquin.com

It should use simple iconography for each one of those fields.

Font styles to use
Other font styles liked:
• Co, Jubilat, Avenir

Colors

Designer to choose colors to be used in the design.

Requirements
Must have
• Clean aesthetic,
• Good use of negative space.
• It should use our company logo, shown in the attached file. It is able to use the negative of that logo (coloured font and white background) and I have attached other acceptable accent colours in a swatch file.
Should not have
• Should not be too busy
• No extraneous text (slogans, tag lines etc)

```html
<!DOCTYPE html>
<html lang="en">
<head>
<meta charset="UTF-8">
<title>Zelquin Business Card</title>
<link href="https://fonts.googleapis.com/css2?family=Montserrat:wght@400;500;600&display=swap" rel="stylesheet">
<style>
  :root {
    --teal: #3db4b1;
    --teal-deep: #36a3a0;
    --white: #f7f7f5;
    --charcoal: #3a3d40;
    --backdrop: #2c2d2f;
  }
  html, body {
    margin: 0;
    padding: 0;
    width: 800px;
    height: 1200px;
    overflow: hidden;
    background: var(--backdrop);
    font-family: "Montserrat", sans-serif;
  }
  .canvas {
    position: relative;
    width: 800px;
    height: 1200px;
  }
  .card {
    position: absolute;
    left: 80px;
    width: 640px;
    height: 366px;
    border-radius: 16px;
    overflow: hidden;
    box-shadow: 0 10px 30px rgba(0,0,0,0.35);
  }
  .card--front {
    top: 150px;
    background: var(--teal);
    display: flex;
    align-items: center;
    justify-content: center;
  }
  .front-wordmark {
    font-weight: 500;
    font-size: 64px;
    letter-spacing: 4px;
    color: var(--teal-deep);
  }
  .card--back {
    top: 684px;
  }
  .back-shapes {
    position: absolute;
    inset: 0;
  }
  .holder {
    position: absolute;
    left: 32px;
    top: 30px;
    color: var(--white);
  }
  .holder-name {
    font-size: 20px;
    font-weight: 500;
    margin: 0;
  }
  .holder-title {
    font-size: 12px;
    margin: 4px 0 0;
    opacity: 0.9;
  }
  .contacts {
    position: absolute;
    left: 32px;
    bottom: 42px;
    list-style: none;
    margin: 0;
    padding: 0;
    color: var(--white);
    font-size: 12px;
  }
  .contacts li {
    display: flex;
    align-items: center;
    gap: 10px;
    margin-top: 6px;
  }
  .contacts svg {
    width: 12px;
    height: 12px;
  }
  .back-wordmark {
    position: absolute;
    left: 340px;
    right: 20px;
    top: 156px;
    text-align: center;
    font-size: 40px;
    font-weight: 500;
    letter-spacing: 3px;
    color: var(--teal);
  }
</style>
</head>
<body>
<div class="canvas">
  <section class="card card--front">
    <span class="front-wordmark">ZELQUIN</span>
  </section>

  <section class="card card--back">
    <svg class="back-shapes" viewBox="0 0 640 366" preserveAspectRatio="none">
      <rect width="640" height="366" fill="var(--teal)"/>
      <path d="M 352 0 C 244 80, 244 290, 322 366 L 640 366 L 640 0 Z" fill="var(--charcoal)"/>
      <path d="M 366 0 C 258 80, 258 290, 336 366 L 640 366 L 640 0 Z" fill="var(--white)"/>
    </svg>

    <div class="holder">
      <p class="holder-name">Mara Lenton</p>
      <p class="holder-title">Managing Director</p>
    </div>

    <ul class="contacts">
      <li>
        <svg viewBox="0 0 12 12"><path d="M3 1 L5 3.5 L4 5 C4.8 6.6 5.6 7.4 7 8 L8.5 7 L11 9 L9.5 11 C5 10.5 1.5 7 1 2.5 Z" fill="var(--white)"/></svg>
        <span>555.014.2273</span>
      </li>
      <li>
        <svg viewBox="0 0 12 12"><rect x="1" y="2.5" width="10" height="7" rx="1" fill="none" stroke="var(--white)" stroke-width="1.2"/><path d="M1.5 3 L6 6.5 L10.5 3" fill="none" stroke="var(--white)" stroke-width="1.2"/></svg>
        <span>mara@zelquin.com</span>
      </li>
      <li>
        <svg viewBox="0 0 12 12"><circle cx="6" cy="6" r="4.8" fill="none" stroke="var(--white)" stroke-width="1.2"/><path d="M1.2 6 H10.8 M6 1.2 C3.8 3.5 3.8 8.5 6 10.8 M6 1.2 C8.2 3.5 8.2 8.5 6 10.8" fill="none" stroke="var(--white)" stroke-width="1"/></svg>
        <span>www.zelquin.com</span>
      </li>
    </ul>

    <div class="back-wordmark">ZELQUIN</div>
  </section>
</div>
</body>
</html>
```